Letterhead for Business Law Firm

We need a letter head for our firm based on the design we have settled on and it is attached. Our clients are small and large businesses around the world, and our letterhead is used typically for formal legal purposes such as demand letters (accusing the recipient of doing bad things) or responding to demand letters. It may also be sent to regulators and other government agencies. So this needs to be tasteful, but a little edgy as well - we try to convey that we are a firm that is different - businesses and investors come to us for creative, quick advice, typically in high stress circumstances, and for our ability to work through high conflict situations, and rapid paced engagements.

Target Market(s)

Lawyers, business executives, investors, government regulators who may receive letters from this firm on behalf of its clients.

Industry/Entity Type

Business

Requirements
Must have
• The design and the firm's contact information:
• Thornwell Law Firm, P.C.
• 1876 NE 57th Ave
• Portland, OR 97213
• phone: 971 555 0147
• fax: 971 555 0182
• in what placement and how depicted (e.g. a phone icon instead of the word "phone") I leave to your creative ideas.
Nice to have
• design and information can be placed at the top, bottom and/or sides of the letter, and the design should be for a standard letter size paper - and can have a separate design for the second page.

```html
<!DOCTYPE html>
<html lang="en">
<head>
<meta charset="utf-8">
<title>Thornwell Letterhead</title>
<link href="https://fonts.googleapis.com/css2?family=Source+Sans+3:wght@400&display=swap" rel="stylesheet">
<style>
  :root {
    --paper: #ffffff;
    --ink: #3a3a3a;
    --ink-dark: #231f20;
    --rule: #9a9a9a;
    --teal: #3f7478;
    --swoosh: #2b2b2b;
  }
  html, body {
    margin: 0;
    padding: 0;
    overflow: hidden;
    background: var(--paper);
  }
  .letterhead {
    position: relative;
    width: 1019px;
    height: 1200px;
    background: var(--paper);
    overflow: hidden;
    font-family: "Source Sans 3", sans-serif;
    color: var(--ink);
  }
  .brand {
    position: absolute;
    left: 62px;
    top: 55px;
    height: 86px;
    display: flex;
    align-items: center;
    gap: 16px;
  }
  .brand-square {
    width: 46px;
    height: 46px;
    background: var(--teal);
  }
  .brand-name {
    font-size: 44px;
    font-weight: 400;
    letter-spacing: 9px;
    color: var(--ink-dark);
    line-height: 1;
  }
  .contact {
    position: absolute;
    left: 810px;
    top: 40px;
    padding-left: 16px;
    border-left: 1px solid var(--rule);
    font-size: 15px;
    line-height: 19px;
    white-space: nowrap;
  }
  .contact p { margin: 0; }
  .contact .address { margin-bottom: 12px; }
  .contact .line {
    display: flex;
    align-items: center;
    gap: 5px;
    line-height: 21px;
  }
  .contact svg { width: 11px; height: 11px; fill: var(--ink); flex: none; }
  .footer-band {
    position: absolute;
    left: 0;
    bottom: 0;
    width: 1019px;
    height: 130px;
  }
  .web {
    position: absolute;
    right: 48px;
    bottom: 30px;
    font-size: 17px;
    letter-spacing: 3.5px;
    color: var(--paper);
  }
</style>
</head>
<body>
<div class="letterhead">
  <div class="brand">
    <div class="brand-square"></div>
    <div class="brand-name">THORNWELL</div>
  </div>

  <div class="contact">
    <p class="address">1876 NE 57th Ave<br>Portland, OR 97213</p>
    <p class="line">
      <svg viewBox="0 0 12 12" aria-hidden="true"><path d="M3 1 L5 3.5 L4 5 Q5 7 7 8 L8.5 7 L11 9 L9.5 11 Q5 11 2.5 8 Q0.5 5 1 2.5 Z"/></svg>
      971 555 0147
    </p>
    <p class="line">
      <svg viewBox="0 0 12 12" aria-hidden="true"><rect x="3" y="1" width="6" height="3"/><rect x="1" y="5" width="10" height="4" rx="1"/><rect x="3" y="8" width="6" height="3"/></svg>
      971 555 0182
    </p>
    <p class="line">
      <svg viewBox="0 0 12 12" aria-hidden="true"><path d="M1 5 L6 1.5 L11 5 V11 H1 Z M2 5.5 L6 8.5 L10 5.5" stroke="#fff" stroke-width="0.8"/></svg>
      info@thornwell.com
    </p>
  </div>

  <svg class="footer-band" viewBox="0 0 1019 130" aria-hidden="true">
    <path fill="var(--teal)" d="M0,30 C150,70 330,104 500,99 C700,90 860,50 1019,40 V130 H0 Z"/>
    <path fill="var(--swoosh)" d="M30,37 C180,82 340,92 500,85 C700,72 850,40 975,36 C850,45 700,82 500,94 C340,101 180,90 30,37 Z"/>
  </svg>
  <div class="web">www.thornwell.com</div>
</div>
</body>
</html>
```